Brenvik Systems PowerPoint Template

Project Title: Professional & Functional PowerPoint Template (.potx) – Brenvik Systems Rebrand

Project Overview:
Brenvik Systems has recently undergone a complete rebranding, including a new logo, website, and visual identity. We need a professional, high-end PowerPoint Template (.potx) that reflects our new look while being highly functional for everyday use.

We previously had a design created, but it was built incorrectly (static images, oversized file, no Master Slides). The goal of this project is to take our new aesthetic and build a "workable" template where layouts are controlled by Master Slides and text is easily editable.

Style & Brand Direction:
The template must be an extension of our new website: https://www.brenvik-systems.example/

Aesthetic: Modern, clean, high-tech, and "Industrial Tech."

Color Palette: Please pull the primary blues, greys, and accent colors directly from the website.

Imagery/Graphics: Use clean lines and subtle tech-inspired gradients. Avoid "clutter."

Tone: Innovative, precise, and professional.

Technical Requirements (Crucial)
Format: Must be delivered as a PowerPoint Template file (** .potx **).

Functionality: All layouts must be built using Slide Masters. Users should be able to click "New Slide" and choose from specific layouts.

Native Elements: Do NOT use full-page background images for text areas. Bullet points must use native PowerPoint list functionality (not individual text boxes).

File Size: The template must be optimized and lightweight.

Fonts: Use standard professional fonts or provide the specific web-safe equivalent used on our site (e.g., Montserrat, Open Sans, etc.).

Required Slide Layouts
Please include a minimum of 10–12 Master layouts, including:
*Title Slide (2-3 variations: Dark and Light)
*Agenda/Table of Contents
*Section Header/Divider Slides
*Standard Text/Bullet Slide
*Two-Column Text Slide
*Image + Text Layouts (Left/Right variations)
*Data/Chart Slide (Styled bar/pie charts that match the brand)
*Process/Timeline Slide (Infographic style)
*Section slide

Attachments Provided
Brand Assets (.zip): Contains our new logo in various formats.

Inspiration/Existing PPT: We have attached the previous design created by our web agency. Note: Use this for visual inspiration ONLY. Do not copy the file structure, as it is technically flawed.

Deliverables
Final .potx file.

All used icons or custom graphics in vector format (if applicable).

Instruction note on any specific fonts used.

Target Market(s)

Internal communication and external (investors, customers)

Industry/Entity Type

Semiconductor, Automotive

Requirements
Must have
• A potx file

```html
<!DOCTYPE html>
<html lang="en">
<head>
<meta charset="utf-8">
<title>Brenvik Systems – Presentation Template</title>
<link rel="stylesheet" href="https://fonts.googleapis.com/css2?family=Poppins:wght@600;700;800&family=Roboto:wght@400;500;700&display=swap">
<style>
  :root{
    --board:#4a4b50;
    --blue:#2440f2;
    --blue-deep:#1a2fd6;
    --navy:#0b1238;
    --ink:#111318;
    --text:#3a3d44;
    --footer:#222326;
    --white:#ffffff;
    --wash:#e6eaff;
    --bar-grey:#4b4d52;
  }
  *{box-sizing:border-box;margin:0;padding:0}
  html,body{width:876px;height:1200px;overflow:hidden;background:var(--board)}
  body{position:relative;font-family:"Roboto",Arial,sans-serif;color:var(--text)}
  .slide{position:absolute;width:363px;height:204px;overflow:hidden;background:var(--white)}
  .abs{position:absolute}
  .display{font-family:"Poppins",Arial,sans-serif;font-weight:700;color:var(--ink);line-height:1}

  .brand{position:absolute;display:flex;align-items:center;font-family:"Poppins",Arial,sans-serif;font-weight:700;line-height:1;color:var(--ink)}
  .brand .mark{display:inline-block;background:var(--blue);margin-right:.25em;width:.72em;height:.72em}
  .brand.on-dark{color:var(--white)}
  .brand.on-dark .mark{background:var(--white)}

  .content{background:linear-gradient(115deg,#ffffff 0%,#ffffff 30%,var(--wash) 62%,#ffffff 100%)}
  .content .rail{left:0;top:0;width:3px;height:204px;background:var(--blue)}
  .content .tab{left:0;top:0;width:15px;height:37px;background:var(--blue)}
  .content .slide-title{left:25px;top:16px;font-size:13px}
  .content .brand{right:17px;top:15px;font-size:17px}
  .footer{left:0;bottom:0;width:341px;height:18px;background:var(--footer);display:flex;align-items:center;padding-left:33px;font-size:5.6px;color:var(--white);gap:4px}
  .footer svg{width:6px;height:6px;fill:var(--white)}
  .footer .sep{margin:0 2px}
  .socials{position:absolute;display:flex;gap:3px}
  .socials i{display:block;border-radius:50%;background:var(--white)}
  .footer .socials{left:291px;top:4.5px}
  .footer .socials i{width:9px;height:9px}
  .page-no{right:0;bottom:0;width:19px;height:18px;background:var(--blue);color:var(--white);font-size:6px;display:flex;align-items:center;justify-content:center}

  .photo{position:absolute}

  .cover-light .panel-rail{left:0;top:53px;width:3px;height:100px;background:var(--blue)}
  .cover-light .brand{left:25px;top:43px;font-size:27px}
  .cover-light .headline{left:25px;top:99px;font-size:12.5px;line-height:21px;font-weight:700}
  .date{font-family:"Poppins",Arial,sans-serif;font-weight:600;color:var(--blue);font-size:9px}

  .cover-dark .brand{left:24px;top:138px;font-size:28px}
  .cover-dark .headline{left:208px;top:137px;font-size:11.5px;line-height:17px;color:var(--white)}

  .agenda-row{position:absolute;left:25px;width:205px;display:flex;align-items:center;font-size:8.5px;color:var(--ink)}
  .agenda-row .label{width:55px}
  .agenda-row .rule{width:58px;height:.5px;background:#b9bcc8}
  .agenda-row .num{margin-left:12px}
  .frame{left:209px;top:43px;width:138px;height:129px;background:var(--blue);padding:6px}
  .frame .photo{position:relative;width:100%;height:100%;border:1.5px solid var(--white)}

  .lead{left:25px;top:40px;width:320px;font-size:7.4px;line-height:12.5px;color:var(--text)}
  .milestone{position:absolute;left:25px;width:165px}
  .milestone h3{display:flex;align-items:center;font-family:"Roboto",Arial,sans-serif;font-weight:500;font-size:7px;color:var(--blue);margin-bottom:3px}
  .milestone h3::before{content:"";width:6.5px;height:6.5px;background:var(--blue);margin-right:4px}
  .milestone p{font-size:3.9px;line-height:7px;color:var(--text)}

  .column{position:absolute;top:41px;width:146px;font-size:7.4px;line-height:12.4px;text-align:justify;color:var(--text)}

  .step{position:absolute;top:58px;width:100px}
  .step .num{position:absolute;left:0;top:0;width:24px;height:25px;background:var(--blue);color:var(--white);font-size:8px;display:flex;align-items:center;justify-content:center;font-weight:500}
  .step h3{position:absolute;left:32px;top:3px;width:80px;font-family:"Roboto",Arial,sans-serif;font-weight:500;font-size:6.8px;color:var(--ink)}
  .step .sub{position:absolute;left:32px;top:13px;width:70px;font-size:4.6px;line-height:7px;color:var(--blue)}
  .step .body{position:absolute;left:0;top:36px;width:86px;font-size:5.2px;line-height:8.4px;text-align:justify;color:var(--text)}

  .divider .brand{left:242px;top:85px;font-size:18px}
  .divider .band{left:134px;top:123px;width:229px;height:31px;background:var(--blue);display:flex;align-items:center;padding-left:18px;font-family:"Poppins",Arial,sans-serif;font-weight:700;font-size:16px;color:var(--white)}

  .note{position:absolute;left:26px;width:160px;display:flex}
  .note .icon{flex:none;width:12px;height:12px;background:var(--blue);margin-right:9px}
  .note p{font-size:5.5px;line-height:10.6px;text-align:justify;color:var(--text)}

  .thanks .side{left:0;top:0;width:164px;height:204px;background:var(--blue)}
  .thanks .brand{left:0;width:164px;justify-content:center;top:36px;font-size:18px}
  .thanks h2{position:absolute;left:0;width:164px;top:72px;text-align:center;font-family:"Poppins",Arial,sans-serif;font-weight:700;font-size:21px;line-height:1.1;color:var(--white)}
  .thanks .contact{position:absolute;left:0;width:164px;font-size:8.3px;display:flex;justify-content:center;align-items:center;gap:5px;color:var(--white)}
  .thanks .contact svg{width:8px;height:8px;fill:var(--white)}
  .thanks .socials{left:59px;top:153px}
  .thanks .socials i{width:13px;height:13px}
</style>
</head>
<body>

<svg width="0" height="0" style="position:absolute">
  <defs>
    <symbol id="icon-phone" viewBox="0 0 24 24"><path d="M6.6 10.8a15.2 15.2 0 0 0 6.6 6.6l2.2-2.2a1 1 0 0 1 1-.25 11.4 11.4 0 0 0 3.6.57 1 1 0 0 1 1 1V20a1 1 0 0 1-1 1A17 17 0 0 1 3 4a1 1 0 0 1 1-1h3.5a1 1 0 0 1 1 1c0 1.25.2 2.45.57 3.6a1 1 0 0 1-.25 1z"/></symbol>
    <symbol id="icon-mail" viewBox="0 0 24 24"><path d="M3 6.2v11.8h18V6.2l-9 7.2z"/><path d="M3 5h18l-9 7.2z"/></symbol>
  </defs>
</svg>

<!-- Cover, light -->
<section class="slide cover-light" style="left:69px;top:65px">
  <div class="abs panel-rail"></div>
  <div class="brand"><span class="mark"></span>BRENVIK</div>
  <h1 class="abs display headline">POWERING PROGRESS<br>ACROSS INDUSTRIES</h1>
  <p class="abs date" style="left:25px;top:147px">MARCH 10,2026</p>
  <div class="photo" role="img" aria-label="Laser sparks inside a blue metal tube" style="left:185px;top:0;width:178px;height:204px;background:radial-gradient(circle at 55% 55%,#0d1440 0%,#0a1030 38%,#1f4bb8 52%,#2a5fd0 75%,#16348e 100%)"></div>
</section>

<!-- Cover, dark -->
<section class="slide cover-dark" style="left:69px;top:281px">
  <div class="photo" role="img" aria-label="Laser sparks inside a blue metal tube, fading into navy" style="left:0;top:0;width:363px;height:204px;background:radial-gradient(ellipse 40% 55% at 50% 30%,#0a0f2e 0%,#0d1640 50%,transparent 70%),linear-gradient(180deg,#2a5ad0 0%,#1a3a9c 40%,#0d1a55 70%,var(--navy) 100%)"></div>
  <div class="brand on-dark"><span class="mark"></span>BRENVIK</div>
  <h1 class="abs display headline">POWERING PROGRESS<br>ACROSS INDUSTRIES</h1>
  <p class="abs date" style="left:208px;top:176px;font-size:8px">MARCH 10,2026</p>
</section>

<!-- Agenda -->
<section class="slide content" style="left:69px;top:497px">
  <div class="abs rail"></div><div class="abs tab"></div>
  <h2 class="abs display slide-title">AGENDA</h2>
  <div class="brand"><span class="mark"></span>BRENVIK</div>
  <div class="agenda-row" style="top:49px"><span class="label">Company</span><span class="rule"></span><span class="num">03</span></div>
  <div class="agenda-row" style="top:67px"><span class="label">Solutions</span><span class="rule"></span><span class="num">04</span></div>
  <div class="agenda-row" style="top:84px"><span class="label">Approach</span><span class="rule"></span><span class="num">05</span></div>
  <div class="agenda-row" style="top:102px"><span class="label">Careers</span><span class="rule"></span><span class="num">06</span></div>
  <div class="agenda-row" style="top:120px"><span class="label">Contact</span><span class="rule"></span><span class="num">07</span></div>
  <div class="abs frame">
    <div class="photo" role="img" aria-label="Worker welding metal in a factory" style="background:radial-gradient(circle at 45% 75%,#f0b27a 0%,#8a5a66 25%,#3a3f6a 55%,#1d2240 100%)"></div>
  </div>
  <div class="abs footer"><svg><use href="#icon-phone"/></svg>+1 888 888 8888<span class="sep">|</span><svg><use href="#icon-mail"/></svg>info@companyname.com<div class="socials"><i></i><i></i><i></i></div></div>
  <div class="abs page-no">02</div>
</section>

<!-- Our story -->
<section class="slide content" style="left:69px;top:714px">
  <div class="abs rail"></div><div class="abs tab"></div>
  <h2 class="abs display slide-title">OUR STORY</h2>
  <div class="brand"><span class="mark"></span>BRENVIK</div>
  <div class="photo" role="img" aria-label="Clean-room manufacturing machines in glass enclosures" style="left:190px;top:60px;width:173px;height:126px;background:linear-gradient(90deg,rgba(255,255,255,1) 0%,rgba(255,255,255,0) 30%),linear-gradient(180deg,#dfe3ea 0%,#8f97a6 45%,#3b404a 100%)"></div>
  <p class="abs lead">For industries driving tech forward, Brenvik is the most advanced laser-based manufacturing partner, unlocking the power of light for cleaner, smarter, more scalable production.</p>
  <div class="milestone" style="top:73px"><h3>2016 - Founded In</h3><p>Founded in 2016, we emerged to replace wasteful mechanical manufacturing with laser precision. Today we deliver 2.2-2.3 wafers per mm with $98M in funding.</p></div>
  <div class="milestone" style="top:112px"><h3>2–3x - Improvement in wafer throughput</h3><p>We don't optimize existing processes—we eliminate them. Our breakthrough approach creates manufacturing methods that seemed impossible years ago.</p></div>
  <div class="milestone" style="top:144px"><h3>+60% - Cost savings at scale</h3><p>From our home campus to facilities worldwide, our process reduces costs by more than 60% while cutting waste—making clean technology more accessible and efficient.</p></div>
  <div class="abs footer"><svg><use href="#icon-phone"/></svg>+1 888 888 8888<span class="sep">|</span><svg><use href="#icon-mail"/></svg>info@companyname.com<div class="socials"><i></i><i></i><i></i></div></div>
  <div class="abs page-no">03</div>
</section>

<!-- Who we are -->
<section class="slide content" style="left:69px;top:930px">
  <div class="abs rail"></div><div class="abs tab"></div>
  <h2 class="abs display slide-title">WHO WE ARE</h2>
  <div class="brand"><span class="mark"></span>BRENVIK</div>
  <p class="column" style="left:26px">Our laser technology achieves precision traditional methods can't, driving clean energy and next-generation computing. We turn light into precision that traditional manufacturing can't achieve. Our breakthrough laser technology enables the clean energy revolution—from EV power electronics to next-generation computing. We need brilliant minds who thrive on solving impossible problems.</p>
  <p class="column" style="left:193px">If you have expertise in Laser Material Processing, Optics Design, Precision Mechanical Design, or Control Systems Software Development, we want to build the future together. Behind every breakthrough is a team, experience, and results that drive us forward. If breakthrough innovation and world-changing technology align with your ambitions, consider Brenvik your next professional home.</p>
  <div class="abs footer"><svg><use href="#icon-phone"/></svg>+1 888 888 8888<span class="sep">|</span><svg><use href="#icon-mail"/></svg>info@companyname.com<div class="socials"><i></i><i></i><i></i></div></div>
  <div class="abs page-no">04</div>
</section>

<!-- Our approach -->
<section class="slide content" style="left:444px;top:173px">
  <div class="abs rail"></div><div class="abs tab"></div>
  <h2 class="abs display slide-title">OUR APPROACH</h2>
  <div class="brand"><span class="mark"></span>BRENVIK</div>
  <div class="step" style="left:19px"><div class="num">01</div><h3>Chart the unseen</h3><p class="sub">CREATE TOMORROW TODAY</p><p class="body">We don't optimize existing processes—we eliminate them. Our laser technology unlocks capabilities that conventional methods can't achieve, enabling previously impossible wafer geometries and specifications.</p></div>
  <div class="step" style="left:131px;top:55px"><div class="num" style="top:3px">02</div><h3 style="top:0">Light your path forward</h3><p class="sub" style="top:10px">PARTNERSHIP WITHOUT COMPROMISE</p><p class="body" style="top:39px">We work together to optimize wafer characteristics for your applications. From discovery to delivery, every specification serves your end goals.</p></div>
  <div class="step" style="left:252px"><div class="num">03</div><h3>Create a ripple effect</h3><p class="sub">CLEAN INNOVATION THAT PERFORMS</p><p class="body">90% waste reduction and superior yield create benefits that ripple through your entire operation—better wafers, better devices, better outcomes.</p></div>
  <div class="abs footer"><svg><use href="#icon-phone"/></svg>+1 888 888 8888<span class="sep">|</span><svg><use href="#icon-mail"/></svg>info@companyname.com<div class="socials"><i></i><i></i><i></i></div></div>
  <div class="abs page-no">05</div>
</section>

<!-- Section divider -->
<section class="slide divider" style="left:444px;top:390px">
  <div class="photo" role="img" aria-label="Laser head cutting a wafer on a dark machine bed" style="left:0;top:0;width:363px;height:204px;background:radial-gradient(ellipse 35% 30% at 38% 70%,#3a5ab8 0%,#1a2550 40%,transparent 75%),linear-gradient(135deg,#2a2e3a 0%,#15171f 45%,#0a0b10 100%)"></div>
  <div class="brand on-dark"><span class="mark"></span>BRENVIK</div>
  <div class="abs band">SECTION DIVIDER TITLE</div>
</section>

<!-- Our graph -->
<section class="slide content" style="left:444px;top:605px">
  <div class="abs rail"></div><div class="abs tab"></div>
  <h2 class="abs display slide-title">OUR GRAPH</h2>
  <div class="brand"><span class="mark"></span>BRENVIK</div>
  <div class="note" style="top:42px"><span class="icon"></span><p>Sed ut perspiciatis unde omnis iste natus error sit voluptatem accusantium doloremque laudantium, totam rem aperiam, eaque ipsa quae ab illo inventore veritatis et quaatae vitae dicta sunt explicabo.</p></div>
  <div class="note" style="top:96px"><span class="icon"></span><p>Nemo enim ipsam voluptatem quia voluptas sit aspernatur aut odit aut fugit, sed quia consequuntur magni dolores eos qui ratione vm sequi nesc.</p></div>
  <div class="note" style="top:139px"><span class="icon"></span><p>Iipsum quia dolor sit amet, consectetur, adipisci velit, sed quia non numquodi tempora incidunt ut labore et dolore magerat volminima veniam quis.</p></div>
  <svg class="abs" style="left:0;top:0" width="363" height="204" viewBox="0 0 363 204" font-family="Roboto, Arial, sans-serif" font-size="3.4" fill="#555">
    <line x1="218" y1="42" x2="218" y2="155" stroke="#9a9ca4" stroke-width=".4"/>
    <line x1="218" y1="155" x2="349" y2="155" stroke="#9a9ca4" stroke-width=".4"/>
    <g text-anchor="end">
      <text x="215" y="156">0</text><text x="215" y="145">1</text><text x="215" y="134">2</text><text x="215" y="123">3</text><text x="215" y="111">4</text><text x="215" y="100">5</text><text x="215" y="89">6</text><text x="215" y="78">7</text><text x="215" y="67">8</text><text x="215" y="56">9</text><text x="215" y="44">10</text>
    </g>
    <rect x="227" y="104.6" width="8" height="50.4" fill="var(--bar-grey)"/>
    <rect x="248" y="99" width="8" height="56" fill="var(--blue)"/>
    <rect x="269" y="75.5" width="8" height="79.5" fill="var(--bar-grey)"/>
    <rect x="290" y="99" width="8" height="56" fill="var(--blue)"/>
    <rect x="311" y="104.6" width="8" height="50.4" fill="var(--bar-grey)"/>
    <rect x="331" y="75.5" width="8" height="79.5" fill="var(--blue)"/>
    <g text-anchor="middle">
      <text x="231" y="102">4.5%</text><text x="252" y="96.5">5%</text><text x="273" y="73">7.1%</text><text x="294" y="96.5">5%</text><text x="315" y="102">4.5%</text><text x="335" y="73">7.1%</text>
      <text x="231" y="160">2000</text><text x="252" y="160">2005</text><text x="273" y="160">2010</text><text x="294" y="160">2015</text><text x="315" y="160">2020</text><text x="335" y="160">2024</text>
    </g>
  </svg>
  <div class="abs footer"><svg><use href="#icon-phone"/></svg>+1 888 888 8888<span class="sep">|</span><svg><use href="#icon-mail"/></svg>info@companyname.com<div class="socials"><i></i><i></i><i></i></div></div>
  <div class="abs page-no">07</div>
</section>

<!-- Thank you -->
<section class="slide thanks" style="left:444px;top:822px">
  <div class="photo" role="img" aria-label="Robotic arm beside server racks in blue light" style="left:164px;top:0;width:199px;height:204px;background:linear-gradient(160deg,#1b2a55 0%,#3d5fa8 40%,#7c9ad0 55%,#22335f 80%,#0e1630 100%)"></div>
  <div class="abs side"></div>
  <div class="brand on-dark"><span class="mark"></span>BRENVIK</div>
  <h2>THANK YOU</h2>
  <p class="contact" style="top:110px"><svg><use href="#icon-phone"/></svg>+1 888 888 8888</p>
  <p class="contact" style="top:125px"><svg><use href="#icon-mail"/></svg>info@companyname.com</p>
  <div class="socials"><i></i><i></i><i></i></div>
</section>

</body>
</html>
```